Website for Ashcombe Tube Drift

Require a website for a river float in the City of Edmonton. Located on North Saskatchewan River. Will need to be a coded website with incorporated booking system through Fare Harbor software.

Pages include
Home
Pricing
About
FAQ
Contact

Ashcombe Tube Drift is an activity based business that will have customers floating down the North Saskatchewan river in Edmonton AB. The site will have all information needed and a full reservation system. The project was launched to provide people in the Edmonton area a favorite summer activity.

Here are similar websites to reference what our business will be doing and what we are looking for.

mossbankfloatco.com
quillpointpaddles.com

Target Market(s)

Families, Groups, Individuals, Anyone who wants to explore the river

Industry/Entity Type

Activities based business/ Outdoor recreational/ River Float

Coding

Coded - Design and coding required

Number of Pages Required

5+ page

Colors
0054AA
0677BA
7BADD7
CADEEF
E8F1F8
F0912C
F2A743
F7CA91
FBE8D2
FDF5EE

```html
<!DOCTYPE html>
<html lang="en">
<head>
<meta charset="utf-8">
<title>Ashcombe Tube Drift</title>
<link rel="stylesheet" href="https://fonts.googleapis.com/css2?family=Lato:wght@400;700;900&display=swap">
<style>
:root{
  --navy:#0c3a6b;
  --navy-deep:#0a2a52;
  --orange:#e2572b;
  --orange-soft:#f0912c;
  --cyan:#4cc3e6;
  --sky:#7badd7;
  --grey-bg:#f7f7f7;
  --text:#444;
  --white:#fff;
  --black:#000;
}
*{box-sizing:border-box;margin:0;padding:0}
html,body{width:1200px;height:3630px;overflow:hidden}
body{position:relative;font-family:'Lato',sans-serif;color:var(--text);background:var(--white)}
.abs{position:absolute}
a{color:inherit;text-decoration:none}

/* hero */
.hero{left:0;top:0;width:1200px;height:641px;
  background:linear-gradient(180deg,#8fa1ad 0%,#b9a58d 30%,#8a8a7a 50%,#3f5a3a 68%,#2e4a44 85%,#3a5a50 100%)}
.hero-rule{left:0;top:645px;width:1200px;height:6px;background:var(--cyan)}
.brand{left:132px;top:20px;width:160px;text-align:center;font-weight:900;font-size:19px;line-height:1.1;color:var(--navy)}
.topbar{top:10px;font-size:12.5px;color:var(--white)}
.topbar svg{vertical-align:-2px;margin-right:5px}
.sep{top:6px;width:1px;height:26px;background:rgba(255,255,255,.7)}
.social-dot{top:13px;width:9px;height:9px;border-radius:50%;background:var(--white)}
.top-line{left:475px;top:45px;width:592px;height:1px;background:rgba(255,255,255,.7)}
.nav{top:60px;font-size:12.5px;font-weight:700;color:var(--white);letter-spacing:.2px}
.nav.active{color:var(--orange)}
.hero-title{left:0;top:228px;width:1200px;text-align:center;font-size:56px;font-weight:700;color:var(--white);letter-spacing:.5px}
.hero-sub{left:0;top:304px;width:1200px;text-align:center;font-size:15px;color:var(--white)}
.btn{display:block;text-align:center;font-weight:700;color:var(--white);border-radius:30px}
.btn-navy{background:linear-gradient(180deg,#2a3f6e,#0a2a52)}
.btn-orange{background:var(--orange)}
.hero-btn{left:520px;top:349px;width:160px;height:48px;line-height:48px;font-size:15px;background:linear-gradient(180deg,#d6552b,#1a2f5a)}
.dot{top:597px;width:12px;height:12px;border-radius:50%;background:var(--white)}

/* pricing */
.price-ring{left:117px;top:724px;width:484px;height:484px;border-radius:50%;border:6px solid var(--orange);border-bottom-color:transparent;border-right-color:transparent;transform:rotate(-10deg)}
.price-photo{left:123px;top:730px;width:472px;height:472px;border-radius:50%;
  background:linear-gradient(180deg,#9cc3de 0%,#cfd8dc 35%,#6b7d8a 60%,#3d4d56 80%,#27404a 100%)}
.badge-circle{left:383px;top:1087px;width:192px;height:192px;border-radius:50%;background:var(--white);box-shadow:0 6px 10px rgba(0,0,0,.25);display:flex;align-items:center;justify-content:center;text-align:center;font-weight:900;font-size:17px;color:var(--navy);padding:20px;line-height:1.2}
.eyebrow{font-size:23px;font-weight:700;color:var(--orange)}
.price-title{left:672px;top:764px;font-size:37px;font-weight:700;color:var(--navy);letter-spacing:.3px}
.price-amount{left:672px;top:816px;font-size:23px;color:var(--cyan)}
.per{left:722px;top:823px;font-size:11.5px;font-weight:700;color:var(--navy)}
.per-link{left:784px;top:823px;font-size:11.5px;font-weight:700;color:var(--orange);text-decoration:underline}
.price-lead{left:674px;top:860px;width:440px;font-size:18px;font-weight:700;color:var(--navy);line-height:28px}
.price-note{left:673px;top:924px;font-size:12.5px;color:var(--orange)}
.include-list{left:673px;top:953px;list-style:none;font-size:13px;color:#333}
.include-list li{height:28px;display:flex;align-items:center}
.include-list svg{margin-right:11px}
.price-btn{left:674px;top:1160px;width:158px;height:48px;line-height:48px;font-size:16px}
.group{left:677px;top:1226px;font-size:15px;color:#444}
.group span{color:var(--orange)}
.tax{left:677px;top:1257px;font-size:12.5px;color:#e2233b}

/* about */
.about{left:0;top:1355px;width:1200px;height:716px;
  background:linear-gradient(180deg,#244a7c 0%,#1f4678 40%,#1c3e6a 70%,#223f5f 100%)}
.about-eyebrow{left:0;top:1428px;width:1200px;text-align:center}
.about-title{left:0;top:1460px;width:1200px;text-align:center;font-size:32px;font-weight:700;color:var(--white);line-height:39px}
.about-sub{left:0;top:1550px;width:1200px;text-align:center;font-size:15.5px;font-weight:700;color:var(--white)}
.about-copy{left:120px;top:1610px;width:470px;font-size:12.3px;line-height:28px;color:var(--white)}
.about-btn{left:120px;top:1942px;width:157px;height:48px;line-height:48px;font-size:16px}
.about-mark{left:624px;top:1626px;width:452px;height:452px;display:flex;align-items:center;justify-content:center}
.about-mark .circle{width:452px;height:452px;border-radius:50%;background:var(--cyan);border:8px solid var(--navy-deep);display:flex;align-items:center;justify-content:center;font-size:38px;font-weight:900;color:var(--navy-deep);text-align:center;line-height:1.15;padding:40px}

/* faq */
.faq{left:0;top:2071px;width:1200px;height:621px;background:var(--grey-bg)}
.faq-title{left:0;top:2148px;width:1200px;text-align:center;font-size:36px;font-weight:700;color:var(--navy)}
.faq-item{left:193px;width:814px;height:52px;background:var(--white);border-radius:8px;box-shadow:0 2px 6px rgba(0,0,0,.06);display:flex;align-items:center;justify-content:space-between;padding:0 30px 0 44px;font-size:13px;font-weight:700;color:#222}
.faq-item.open{box-shadow:0 4px 12px rgba(0,0,0,.22)}

/* contact */
.contact-title{left:145px;top:2812px;font-size:28px;font-weight:700;color:var(--navy)}
.contact-sub{left:145px;top:2856px;font-size:20px;color:var(--orange)}
.c-icon{width:42px;height:42px;border-radius:50%;background:var(--orange);display:flex;align-items:center;justify-content:center}
.c-text{font-size:14px;color:#555}
.map{left:605px;top:2777px;width:448px;height:314px;border-radius:14px;box-shadow:0 4px 12px rgba(0,0,0,.25);
  background:linear-gradient(135deg,#eef0f2,#e6e9ec);border:4px solid var(--white)}

/* footer */
.foot-rule{left:0;top:3211px;width:1200px;height:6px;background:var(--cyan)}
.footer{left:0;top:3220px;width:1200px;height:410px;background:var(--black)}
.foot-brand{left:140px;top:3404px;width:180px;text-align:center;font-size:20px;font-weight:900;color:var(--cyan);line-height:1.15}
.foot-brand-dot{left:198px;top:3330px;width:64px;height:64px;border-radius:50%;background:var(--cyan)}
.foot-social{top:3480px;width:30px;height:30px;border-radius:50%;background:var(--orange)}
.foot-head{top:3313px;font-size:15.5px;font-weight:700;color:var(--white)}
.foot-links{left:381px;top:3341px;list-style:none;font-size:14px;color:var(--white)}
.foot-links li{height:28px;display:flex;align-items:center}
.foot-links svg{margin-right:14px}
.f-icon{width:30px;height:30px;border-radius:50%;background:var(--orange);display:flex;align-items:center;justify-content:center}
.f-text{font-size:13.5px;color:var(--white)}
.news-copy{left:807px;top:3343px;width:250px;font-size:13px;line-height:28px;color:var(--white)}
.news-input{left:807px;top:3407px;width:201px;height:38px;background:var(--white);border:1px solid #ccc;font-size:11px;color:#999;padding:0 12px;line-height:36px}
.news-btn{left:1008px;top:3407px;width:51px;height:38px;background:var(--orange);display:flex;align-items:center;justify-content:center}
.hours-badge{left:887px;top:3464px;width:106px;height:62px;border:3px solid var(--white);border-radius:50%}
.foot-line{left:103px;top:3552px;width:995px;height:1px;background:#555}
.copyright{left:0;top:3575px;width:1200px;text-align:center;font-size:12px;color:var(--white)}
</style>
</head>
<body>

<!-- Hero -->
<div class="abs hero" role="img" aria-label="Photo of the downtown Edmonton skyline and bridge over the North Saskatchewan River at dusk"></div>
<div class="abs brand">ASHCOMBE TUBE DRIFT</div>

<div class="abs topbar" style="left:470px"><svg width="11" height="11" viewBox="0 0 24 24" fill="#fff"><path d="M6.6 10.8a15 15 0 0 0 6.6 6.6l2.2-2.2c.3-.3.7-.4 1-.2 1.1.4 2.3.6 3.6.6.6 0 1 .4 1 1V20c0 .6-.4 1-1 1A17 17 0 0 1 3 4c0-.6.4-1 1-1h3.5c.6 0 1 .4 1 1 0 1.3.2 2.5.6 3.6.1.3 0 .7-.2 1z"/></svg>+1 555 014 2076</div>
<div class="abs sep" style="left:613px"></div>
<div class="abs topbar" style="left:635px"><svg width="12" height="11" viewBox="0 0 24 20" fill="#fff"><path d="M2 2h20v2l-10 7L2 4zm0 4 10 7 10-7v12H2z"/></svg>info@ashcombetubedrift.com</div>
<div class="abs sep" style="left:855px"></div>
<div class="abs topbar" style="left:876px"><svg width="11" height="11" viewBox="0 0 24 24" fill="#fff"><path d="M10 5l7 7-7 7v-4H2V9h8zM14 3h7v18h-7v-2h5V5h-5z"/></svg>Login</div>
<div class="abs sep" style="left:946px"></div>
<div class="abs social-dot" style="left:984px"></div>
<div class="abs social-dot" style="left:1002px"></div>
<div class="abs social-dot" style="left:1022px"></div>
<div class="abs social-dot" style="left:1042px"></div>
<div class="abs top-line"></div>
<a class="abs nav active" style="left:680px">HOME</a>
<a class="abs nav" style="left:751px">ABOUT US</a>
<a class="abs nav" style="left:846px">PRICING</a>
<a class="abs nav" style="left:931px">FAQ</a>
<a class="abs nav" style="left:987px">CONTACT US</a>

<h1 class="abs hero-title">ASHCOMBE TUBE DRIFT</h1>
<p class="abs hero-sub">Float the North Saskatchewan through downtown Edmonton</p>
<a class="abs btn hero-btn">BOOK NOW</a>
<span class="abs dot" style="left:578px;background:var(--orange)"></span>
<span class="abs dot" style="left:593px"></span>
<span class="abs dot" style="left:608px"></span>
<div class="abs hero-rule"></div>

<!-- Pricing -->
<div class="abs price-photo" role="img" aria-label="Photo of a steel arch bridge over a marina with moored boats and city towers"></div>
<div class="abs price-ring"></div>
<div class="abs badge-circle">ASHCOMBE TUBE DRIFT</div>

<h2 class="abs eyebrow" style="left:672px;top:734px">OUR PRICING</h2>
<h3 class="abs price-title">TUBE AND SHUTTLE</h3>
<div class="abs price-amount">$30</div>
<div class="abs per">/PERSON</div>
<a class="abs per-link">BOOK NOW</a>
<p class="abs price-lead">WE KEEP OUR PRICING SIMPLE AND INCLUDE EVERYTHING YOU NEED:</p>
<p class="abs price-note">Premium comfort float tube with backrest and cup holder</p>
<ul class="abs include-list">
  <li><svg width="14" height="14" viewBox="0 0 14 14"><circle cx="7" cy="7" r="7" fill="#e2572b"/><path d="M5.5 4l3 3-3 3" stroke="#fff" stroke-width="1.8" fill="none"/></svg>Lifejacket</li>
  <li><svg width="14" height="14" viewBox="0 0 14 14"><circle cx="7" cy="7" r="7" fill="#e2572b"/><path d="M5.5 4l3 3-3 3" stroke="#fff" stroke-width="1.8" fill="none"/></svg>Paddle</li>
  <li><svg width="14" height="14" viewBox="0 0 14 14"><circle cx="7" cy="7" r="7" fill="#e2572b"/><path d="M5.5 4l3 3-3 3" stroke="#fff" stroke-width="1.8" fill="none"/></svg>Round trip shuttle service</li>
  <li><svg width="14" height="14" viewBox="0 0 14 14"><circle cx="7" cy="7" r="7" fill="#e2572b"/><path d="M5.5 4l3 3-3 3" stroke="#fff" stroke-width="1.8" fill="none"/></svg>Safety training</li>
  <li><svg width="14" height="14" viewBox="0 0 14 14"><circle cx="7" cy="7" r="7" fill="#e2572b"/><path d="M5.5 4l3 3-3 3" stroke="#fff" stroke-width="1.8" fill="none"/></svg>Staff assistance</li>
  <li><svg width="14" height="14" viewBox="0 0 14 14"><circle cx="7" cy="7" r="7" fill="#e2572b"/><path d="M5.5 4l3 3-3 3" stroke="#fff" stroke-width="1.8" fill="none"/></svg>Parking</li>
  <li><svg width="14" height="14" viewBox="0 0 14 14"><circle cx="7" cy="7" r="7" fill="#e2572b"/><path d="M5.5 4l3 3-3 3" stroke="#fff" stroke-width="1.8" fill="none"/></svg>Unlimited Fun!</li>
</ul>
<a class="abs btn btn-navy price-btn">BOOK NOW</a>
<p class="abs group">Group of 10 or more? <span>Contact us</span></p>
<p class="abs tax">*does not include taxes or fees</p>

<!-- About -->
<div class="abs about" role="img" aria-label="Aerial photo of the river valley and city under cloudy sky, tinted navy"></div>
<h2 class="abs eyebrow about-eyebrow">ABOUT US</h2>
<h3 class="abs about-title">FLOAT THE NORTH SASKATCHEWAN THROUGH<br>DOWNTOWN EDMONTON</h3>
<p class="abs about-sub">Edmonton’s Best Summer Activity</p>
<p class="abs about-copy">We provide the lifejacket, paddle, river tube and shuttle service. You just have to show up. Ashcombe Tube Drift was launched to provide people in the Edmonton area a favorite summer activity. Nothing is better on a hot summer day, than spending it on the river and seeing Edmonton from a new perspective. Our home base and meeting spot is at Heron Landing (Map Link), by the Kestrel Glasshouse. This is where you will check in, and board the shuttle. The shuttle will take all floaters up river to Birchwell Park Boat Launch, where your tube will be waiting. Once on the river, you can sit back, relax, explore and enjoy the view. Once you complete the float, and arrive back at Heron Landing, staff will be available to assist in exiting the river where you will return your tube and gear. Safety is our top priority, but having fun is a close second. Don’t miss out on Edmonton’s best summer activity.</p>
<a class="abs btn btn-orange about-btn">BOOK NOW</a>
<div class="abs about-mark"><div class="circle">ASHCOMBE TUBE DRIFT</div></div>

<!-- FAQ -->
<div class="abs faq"></div>
<h2 class="abs faq-title">FREQUENTLY ASKED QUESTIONS</h2>
<div class="abs faq-item open" style="top:2232px">HOW DO I RESERVE MY FLOAT?<span>+</span></div>
<div class="abs faq-item" style="top:2303px">WHAT SAFETY INFORMATION SHOULD I KNOW?<span>+</span></div>
<div class="abs faq-item" style="top:2375px">WHAT IS INCLUDED?<span>+</span></div>
<div class="abs faq-item" style="top:2447px">WHAT SHOULD I BRING?<span>+</span></div>
<div class="abs faq-item" style="top:2519px">WHERE ARE YOU LOCATED?<span>+</span></div>

<!-- Contact -->
<h2 class="abs contact-title">CONTACT US</h2>
<p class="abs contact-sub">We’d love to hear from you!</p>
<div class="abs c-icon" style="left:146px;top:2905px"><svg width="16" height="18" viewBox="0 0 24 24" fill="#fff"><path d="M12 2a7 7 0 0 0-7 7c0 5 7 13 7 13s7-8 7-13a7 7 0 0 0-7-7zm0 9.5a2.5 2.5 0 1 1 0-5 2.5 2.5 0 0 1 0 5z"/></svg></div>
<p class="abs c-text" style="left:212px;top:2917px">412 Ferrow Ave NW, Edmonton, AB</p>
<div class="abs c-icon" style="left:146px;top:2968px"><svg width="16" height="14" viewBox="0 0 24 20" fill="#fff"><path d="M2 2h20v2l-10 7L2 4zm0 4 10 7 10-7v12H2z"/></svg></div>
<p class="abs c-text" style="left:209px;top:2980px">info@ashcombetubedrift.com</p>
<div class="abs c-icon" style="left:146px;top:3029px"><svg width="16" height="16" viewBox="0 0 24 24" fill="#fff"><path d="M6.6 10.8a15 15 0 0 0 6.6 6.6l2.2-2.2c.3-.3.7-.4 1-.2 1.1.4 2.3.6 3.6.6.6 0 1 .4 1 1V20c0 .6-.4 1-1 1A17 17 0 0 1 3 4c0-.6.4-1 1-1h3.5c.6 0 1 .4 1 1 0 1.3.2 2.5.6 3.6.1.3 0 .7-.2 1z"/></svg></div>
<p class="abs c-text" style="left:209px;top:3041px">+ 1 555 014 2076</p>
<div class="abs map" role="img" aria-label="Map of the river region showing lakes and waterways"></div>

<!-- Footer -->
<div class="abs foot-rule"></div>
<div class="abs footer"></div>
<div class="abs foot-brand-dot"></div>
<div class="abs foot-brand">ASHCOMBE<br>TUBE DRIFT</div>
<div class="abs foot-social" style="left:169px"></div>
<div class="abs foot-social" style="left:212px"></div>
<div class="abs foot-social" style="left:254px"></div>

<h4 class="abs foot-head" style="left:381px">QUICK LINKS</h4>
<ul class="abs foot-links">
  <li><svg width="10" height="10" viewBox="0 0 10 10"><path d="M1 1l3 4-3 4M5 1l3 4-3 4" stroke="#fff" stroke-width="1.5" fill="none"/></svg>Home</li>
  <li><svg width="10" height="10" viewBox="0 0 10 10"><path d="M1 1l3 4-3 4M5 1l3 4-3 4" stroke="#fff" stroke-width="1.5" fill="none"/></svg>Pricing</li>
  <li><svg width="10" height="10" viewBox="0 0 10 10"><path d="M1 1l3 4-3 4M5 1l3 4-3 4" stroke="#fff" stroke-width="1.5" fill="none"/></svg>About</li>
  <li><svg width="10" height="10" viewBox="0 0 10 10"><path d="M1 1l3 4-3 4M5 1l3 4-3 4" stroke="#fff" stroke-width="1.5" fill="none"/></svg>FAQ</li>
  <li><svg width="10" height="10" viewBox="0 0 10 10"><path d="M1 1l3 4-3 4M5 1l3 4-3 4" stroke="#fff" stroke-width="1.5" fill="none"/></svg>Contact</li>
</ul>

<h4 class="abs foot-head" style="left:541px">CONTACT US</h4>
<div class="abs f-icon" style="left:540px;top:3352px"><svg width="12" height="14" viewBox="0 0 24 24" fill="#fff"><path d="M12 2a7 7 0 0 0-7 7c0 5 7 13 7 13s7-8 7-13a7 7 0 0 0-7-7zm0 9.5a2.5 2.5 0 1 1 0-5 2.5 2.5 0 0 1 0 5z"/></svg></div>
<p class="abs f-text" style="left:583px;top:3359px">412 Ferrow Ave NW, Edmonton, AB</p>
<div class="abs f-icon" style="left:540px;top:3411px"><svg width="13" height="13" viewBox="0 0 24 24" fill="#fff"><path d="M6.6 10.8a15 15 0 0 0 6.6 6.6l2.2-2.2c.3-.3.7-.4 1-.2 1.1.4 2.3.6 3.6.6.6 0 1 .4 1 1V20c0 .6-.4 1-1 1A17 17 0 0 1 3 4c0-.6.4-1 1-1h3.5c.6 0 1 .4 1 1 0 1.3.2 2.5.6 3.6.1.3 0 .7-.2 1z"/></svg></div>
<p class="abs f-text" style="left:583px;top:3418px">+1 555 014 2076</p>
<div class="abs f-icon" style="left:540px;top:3466px"><svg width="13" height="11" viewBox="0 0 24 20" fill="#fff"><path d="M2 2h20v2l-10 7L2 4zm0 4 10 7 10-7v12H2z"/></svg></div>
<p class="abs f-text" style="left:583px;top:3473px">info@ashcombetubedrift.com</p>

<h4 class="abs foot-head" style="left:798px">SIGN UP FOR OUR NEWSLETTER</h4>
<p class="abs news-copy">Lorem ipsum dolor sit amet, consectet ur adipiscing elit, sed do.</p>
<div class="abs news-input">Enter The Email</div>
<div class="abs news-btn"><svg width="16" height="16" viewBox="0 0 24 24" fill="#fff"><path d="M22 2 2 11l7 3 2 8 3-6 6 4z"/></svg></div>
<div class="abs hours-badge"></div>

<div class="abs foot-line"></div>
<p class="abs copyright">© Copyrights 2022 &nbsp;Ashcombe Tube Drift | &nbsp; All Rights Reserved</p>

</body>
</html>
```